Business Card Design

We would like to re-design our business cards. Our Company - Qwinrel Turbochargers, rebuilds turbochargers and sells replacement parts. Our website is: http://www.qwinrelturbochargers-example.com
We just had our logo changed. I will attach the file. Looking for fresh new/modern business card. We like the colors red, black, white and silver. Black background looks attractive, but not a requirement. The final design should communicate reasonable/competitive prices, top quality and reliability of our products.
Updates
Project Deadline Extended
Reason: Need to finalize the info on the card. Currently working on changing address and email info. Want to make sure it is the correct one before accepting the final design. Unless, this is something that can be changed at a later time..??
Industry/Entity Type
Business
Contact Information for Business Card
QWINREL TURBOCHARGERS, LLC
20473 Harwick Lane NE
Massillon, OH 44647
Tel: +1-555-214-7390
Fax: +1-555-267-1842
info@QwinrelTurbochargers-example.com
Our current business card had the following highlights:
*We rebuild all Turbocharges for Automotive, Diesel and Industrial
*Precision Balancing and in-house turbocharger needs
*All Turbocharger replacement parts are made in USA / U.K.
Look and feel
Each slider illustrates characteristics of the customer's brand and the style your logo design should communicate.

```html
<!DOCTYPE html>
<html lang="en">
<head>
<meta charset="utf-8">
<title>Qwinrel Turbochargers – Business Card</title>
<link href="https://fonts.googleapis.com/css2?family=Roboto+Slab:wght@400;700&family=Arimo:wght@400&display=swap" rel="stylesheet">
<style>
  :root {
    --red: #e3212a;
    --black: #0b0b0b;
    --white: #ffffff;
    --silver: #d9d9d9;
    --page: #ececec;
    --ink: #1a1a1a;
  }
  * { margin: 0; padding: 0; box-sizing: border-box; }
  html, body { width: 1200px; height: 973px; overflow: hidden; background: var(--page); }
  .stage { position: relative; width: 1200px; height: 973px; }

  .card {
    position: absolute; left: 320px; width: 560px; height: 320px;
    overflow: hidden; box-shadow: 0 4px 14px rgba(0,0,0,.18);
  }
  .card-front { top: 126px; background: var(--white); }
  .card-back  { top: 526px; background: var(--black); }
  .card svg.shapes { position: absolute; inset: 0; }

  .wordmark {
    position: absolute; display: flex; align-items: center; gap: 12px;
    font-family: "Roboto Slab", serif; font-weight: 700; font-size: 30px; line-height: 1;
  }
  .wordmark-mark { width: 22px; height: 22px; background: var(--red); flex: none; }
  .card-front .wordmark { left: 56px; top: 58px; color: var(--black); }
  .card-back .wordmark { left: 0; right: 0; top: 120px; justify-content: center; color: var(--white); }

  .contact {
    position: absolute; right: 38px; top: 180px; text-align: right; font-style: normal;
    font-family: "Arimo", sans-serif; font-size: 15px; line-height: 23px; color: var(--white);
  }
  .contact-company {
    font-family: "Roboto Slab", serif; font-weight: 700; color: var(--red);
    text-decoration: underline;
  }
  .person { position: absolute; left: 40px; top: 244px; }
  .person-name { font-family: "Roboto Slab", serif; font-weight: 700; font-size: 18px; color: var(--red); }
  .person-role { font-family: "Arimo", sans-serif; font-size: 16px; color: var(--white); margin-top: 4px; }

  .website {
    position: absolute; left: 130px; right: 40px; top: 262px; text-align: center;
    font-family: "Roboto Slab", serif; font-size: 16px; color: var(--ink);
  }
</style>
</head>
<body>
<main class="stage">

  <section class="card card-front" aria-label="Business card front">
    <svg class="shapes" width="560" height="320" viewBox="0 0 560 320" aria-hidden="true">
      <polygon points="0,162 200,162 224,138 560,138 560,150 230,150 206,174 0,174" fill="var(--red)"/>
      <polygon points="0,174 206,174 230,150 560,150 560,320 0,320" fill="var(--black)"/>
    </svg>
    <div class="wordmark"><span class="wordmark-mark"></span><span>Qwinrel Turbochargers</span></div>
    <div class="person">
      <p class="person-name">Corvan Ellet</p>
      <p class="person-role">Partner</p>
    </div>
    <address class="contact">
      <p class="contact-company">Qwinrel Turbochargers</p>
      <p>20473 Harwick Lane NE,</p>
      <p>Dunmarra Ohio 40918</p>
      <p>Tel: 555-214-7390</p>
      <p>info@qwinrelturbochargers-example.com</p>
    </address>
  </section>

  <section class="card card-back" aria-label="Business card back">
    <svg class="shapes" width="560" height="320" viewBox="0 0 560 320" aria-hidden="true">
      <polygon points="96,244 490,244 514,224 560,224 560,294 128,294" fill="var(--white)"/>
      <polygon points="490,244 514,224 560,224 560,232 518,232 498,250" fill="var(--red)"/>
      <polygon points="0,252 96,252 128,294 560,294 560,320 0,320" fill="var(--red)"/>
    </svg>
    <div class="wordmark"><span class="wordmark-mark"></span><span>Qwinrel Turbochargers</span></div>
    <p class="website">www.qwinrelturbochargers-example.com</p>
  </section>

</main>
</body>
</html>
```